Brightwave Reach - Business Card

We need a business card for a Social Media Marketing company that specializes in online marketing for small businesses in Canada using common Social Media platforms such as Pixlora, Chatterly, Blinkpost & Quibber.

I have uploaded a copy of our logo which I would like utilized in the business card. We would like the business card to be modern yet classy design.

Our website is www.brightwavereach.ca

Industry/Entity Type

Marketing

Contact Information for Business Card

Email: info@brightwavereach.ca
Website: www.brightwavereach.ca
Telephone: 604-555-0193

Colors

Designer to choose colors to be used in the design.

Requirements
Must have
• Social Media icons on reverse
• Please add some designs with color.

```html
<!DOCTYPE html>
<html lang="en">
<head>
<meta charset="utf-8">
<title>Brightwave Reach – Business Card</title>
<link rel="stylesheet" href="https://fonts.googleapis.com/css2?family=Didact+Gothic&display=swap">
<style>
  :root {
    --page: #e6e3df;
    --card-black: #0b0b0b;
    --card-glow: #2a2a2a;
    --band-grey: #2b2b2b;
    --band-grey-dark: #1a1a1a;
    --silver: #cfcfcf;
    --silver-dim: #6d6d6d;
    --ink-grey: #6e6e6e;
    --ink-grey-light: #8a8a8a;
  }
  * { box-sizing: border-box; margin: 0; padding: 0; }
  html, body {
    width: 1200px;
    height: 784px;
    overflow: hidden;
    background: var(--page);
    font-family: "Didact Gothic", "Century Gothic", sans-serif;
  }
  .sheet {
    width: 1200px;
    height: 784px;
    display: flex;
    align-items: center;
    justify-content: center;
    gap: 40px;
  }
  .card {
    position: relative;
    width: 540px;
    height: 309px;
    overflow: hidden;
    box-shadow: 0 10px 24px rgba(0,0,0,.25);
  }

  /* Front */
  .card--front {
    background: radial-gradient(ellipse at 50% 30%, var(--card-glow) 0%, var(--card-black) 65%);
    display: flex;
    flex-direction: column;
    align-items: center;
    justify-content: center;
    gap: 34px;
  }
  .brand {
    display: flex;
    align-items: center;
    gap: 12px;
    color: var(--ink-grey);
  }
  .brand__mark {
    width: 22px;
    height: 22px;
    border: 2px solid var(--ink-grey);
  }
  .brand__name {
    font-size: 30px;
    letter-spacing: 1px;
    text-transform: uppercase;
  }
  .social {
    display: flex;
    gap: 18px;
    list-style: none;
    color: var(--ink-grey);
    font-size: 12px;
    letter-spacing: .5px;
  }
  .social li { display: flex; align-items: center; gap: 5px; }
  .social__dot {
    width: 9px; height: 9px;
    background: var(--ink-grey);
  }

  /* Back */
  .card--back {
    background: linear-gradient(180deg, var(--band-grey) 0%, var(--band-grey-dark) 100%);
  }
  .band {
    position: absolute;
    left: 0; right: 0;
    top: 66px;
    height: 176px;
    background: linear-gradient(90deg, #050505 0%, #141414 55%, #050505 100%);
    border-top: 3px solid var(--silver);
    border-bottom: 3px solid var(--silver);
    box-shadow: 0 0 6px rgba(255,255,255,.15);
    display: flex;
    align-items: center;
  }
  .band .brand {
    width: 290px;
    justify-content: center;
  }
  .band .brand__name { font-size: 22px; }
  .band .brand__mark { width: 18px; height: 18px; }
  .divider {
    width: 1px;
    height: 120px;
    background: var(--silver-dim);
  }
  .contact {
    list-style: none;
    padding-left: 26px;
    color: var(--ink-grey-light);
    font-size: 15px;
    line-height: 1.55;
  }
  .contact__phone { font-size: 18px; letter-spacing: .5px; }
</style>
</head>
<body>
  <main class="sheet">
    <section class="card card--front" aria-label="Card front">
      <div class="brand">
        <span class="brand__mark"></span>
        <span class="brand__name">Brightwave Reach</span>
      </div>
      <ul class="social">
        <li><span class="social__dot"></span>Pixlora</li>
        <li><span class="social__dot"></span>Chatterly</li>
        <li><span class="social__dot"></span>Quibber</li>
      </ul>
    </section>

    <section class="card card--back" aria-label="Card back">
      <div class="band">
        <div class="brand">
          <span class="brand__mark"></span>
          <span class="brand__name">Brightwave Reach</span>
        </div>
        <div class="divider"></div>
        <ul class="contact">
          <li class="contact__phone">604-555-0193</li>
          <li>info@brightwavereach.ca</li>
          <li>www.brightwavereach.ca</li>
        </ul>
      </div>
    </section>
  </main>
</body>
</html>
```